Bright Horizon; Teaching Series Art.

Our church is going to be teaching a series of messages under the topic/title: Bright Horizon. Just looking for a simple design to help with this. I have uploaded a design that is an example of what we were thinking.

The point of the design is to communicate a new way of doing things (given some of the impact of the coronavirus) - although the background doesn't need to be too busy - just something simple, clean and modern.

Even though it's for a church, we don't need any religious art in the background (crosses, people praying, etc.) Looking for a similar feel background to the one we uploaded.

The only text should be Bright Horizon and maybe highlighting the word New somehow.

Font styles to use
Sans Serif

Requirements
Must have
• Title of "Bright Horizon" - no other text.

```html
<!DOCTYPE html>
<html lang="en">
<head>
<meta charset="utf-8">
<title>Bright Horizon — Teaching Series</title>
<link rel="stylesheet" href="https://fonts.googleapis.com/css2?family=Montserrat:wght@500;600&display=swap">
<style>
  :root {
    --paper: #efefef;
    --paper-shade: #e6e6e6;
    --slate: #345368;
    --slate-soft: #5a7385;
    --vermilion: #da452e;
    --vermilion-soft: #e9a79c;
  }
  html, body {
    margin: 0;
    padding: 0;
    overflow: hidden;
  }
  body {
    width: 1200px;
    height: 675px;
  }
  .series-art {
    position: relative;
    width: 1200px;
    height: 675px;
    overflow: hidden;
    background: radial-gradient(ellipse at 50% 45%, var(--paper) 0%, var(--paper) 55%, var(--paper-shade) 100%);
  }
  .block-grid {
    position: absolute;
    inset: 0;
  }
  .series-title {
    margin: 0;
  }
  .title-word {
    position: absolute;
    margin: 0;
    font-family: "Montserrat", sans-serif;
    line-height: 1;
    white-space: nowrap;
  }
  .title-word--accent {
    left: 402px;
    top: 253px;
    font-size: 58px;
    font-weight: 600;
    color: var(--vermilion);
    letter-spacing: -0.5px;
  }
  .title-word--main {
    left: 402px;
    top: 350px;
    font-size: 80px;
    font-weight: 500;
    color: var(--slate);
  }
</style>
</head>
<body>
  <main class="series-art">
    <svg class="block-grid" width="1200" height="675" viewBox="0 0 1200 675" aria-hidden="false">
      <defs>
        <linearGradient id="stack-tones" x1="0" y1="0" x2="0" y2="1">
          <stop offset="0" stop-color="var(--vermilion)"/>
          <stop offset="1" stop-color="var(--slate)"/>
        </linearGradient>
        <linearGradient id="pair-tones" x1="0" y1="0" x2="1" y2="0">
          <stop offset="0" stop-color="var(--vermilion)"/>
          <stop offset="1" stop-color="var(--slate)"/>
        </linearGradient>
      </defs>

      <!-- top row -->
      <rect class="tall-column" x="286" y="129" width="105" height="209" fill="var(--slate)"/>
      <rect role="img" aria-label="column of small white plus marks" x="333" y="135" width="14" height="196" fill="var(--slate-soft)"/>
      <rect role="img" aria-label="dark geometric accent at the top edge" x="391" y="129" width="104" height="52" fill="var(--slate)" opacity="0.55"/>
      <rect class="square" x="495" y="129" width="105" height="104" fill="var(--slate)"/>
      <rect class="square" x="705" y="129" width="104" height="104" fill="var(--slate)"/>

      <!-- middle band -->
      <rect class="band" x="600" y="233" width="105" height="105" fill="var(--slate)"/>
      <rect role="img" aria-label="geometric accent in red and slate" x="705" y="233" width="104" height="105" fill="url(#pair-tones)"/>

      <!-- decorative stack area -->
      <rect role="img" aria-label="stacked decorative pattern in red and slate" x="819" y="143" width="85" height="180" fill="url(#stack-tones)" opacity="0.85"/>

      <!-- dot beside title -->
      <circle class="title-dot" cx="338" cy="390" r="31.5" fill="var(--vermilion)"/>

      <!-- bottom row -->
      <rect class="square" x="286" y="443" width="105" height="104" fill="var(--slate)"/>
      <rect role="img" aria-label="red geometric accent" x="391" y="443" width="104" height="104" fill="var(--vermilion-soft)"/>
      <rect class="square" x="495" y="443" width="105" height="104" fill="var(--slate)"/>
      <rect role="img" aria-label="grid of small red plus marks" x="624" y="447" width="56" height="96" fill="var(--vermilion)" opacity="0.22"/>

      <!-- corner block with stripe -->
      <rect class="corner-upright" x="809" y="338" width="105" height="209" fill="var(--slate)"/>
      <rect class="corner-foot" x="705" y="443" width="104" height="104" fill="var(--slate)"/>
      <rect class="stripe" x="854" y="338" width="15" height="209" fill="var(--vermilion)"/>
    </svg>

    <h1 class="series-title">
      <span class="title-word title-word--accent">bright</span>
      <span class="title-word title-word--main">HORIZON</span>
    </h1>
  </main>
</body>
</html>
```